Business card design for Brivo Engineering Tandem

We need a new business card design along with all the necessary to place an order. The company is Brivo Engineering Tandem and we recently updated our logo.

```html
<!DOCTYPE html>
<html lang="en">
<head>
<meta charset="utf-8">
<title>Brivo Engineering Tandem – Business Card</title>
<link href="https://fonts.googleapis.com/css2?family=Kanit:wght@400;600;700&display=swap" rel="stylesheet">
<style>
  :root {
    --backdrop: #3b3b3d;
    --card: #1e1e1e;
    --yellow: #e2bd27;
    --grey: #8f8f8d;
    --white: #ffffff;
  }
  * { margin: 0; padding: 0; box-sizing: border-box; }
  html, body {
    width: 1200px;
    height: 1059px;
    overflow: hidden;
    background: var(--backdrop);
    font-family: "Kanit", sans-serif;
  }
  .card {
    position: absolute;
    background: var(--card);
    border-radius: 18px;
    overflow: hidden;
  }
  .card--front { left: 256px; top: 100px; width: 688px; height: 393px; }
  .card--back  { left: 253px; top: 535px; width: 694px; height: 397px; }

  .brand {
    position: absolute;
    display: flex;
    align-items: center;
    gap: 12px;
  }
  .brand__mark {
    width: 16px;
    height: 16px;
    background: var(--yellow);
    flex: none;
  }
  .brand__name {
    color: var(--grey);
    font-weight: 600;
    text-transform: uppercase;
    letter-spacing: 1px;
    line-height: 1.1;
  }
  .card--front .brand { left: 28px; top: 38px; }
  .card--front .brand__name { font-size: 27px; }

  .accent-bar {
    position: absolute;
    left: 0; top: 154px;
    width: 14px; height: 53px;
    background: var(--yellow);
  }
  .person {
    position: absolute;
    left: 28px; top: 146px;
    color: var(--white);
  }
  .person__name {
    color: var(--yellow);
    font-size: 31px;
    font-weight: 700;
    line-height: 1.1;
  }
  .person__role { font-size: 17px; font-weight: 400; margin-top: 2px; }

  .address {
    position: absolute;
    left: 28px; top: 226px;
    color: var(--white);
    font-size: 17px;
    line-height: 28px;
    font-style: normal;
  }
  .contacts {
    position: absolute;
    left: 28px; top: 292px;
    list-style: none;
    color: var(--white);
    font-size: 17px;
  }
  .contacts li {
    display: flex;
    align-items: center;
    gap: 8px;
    height: 27.5px;
  }
  .contacts svg { width: 14px; height: 14px; fill: var(--yellow); flex: none; }

  .decoration { position: absolute; top: 0; bottom: 0; }
  .card--front .decoration {
    right: 0;
    width: 340px;
    background: linear-gradient(180deg, var(--yellow) 0%, #b9a23c 50%, var(--grey) 100%);
  }
  .card--back .decoration {
    left: 0;
    width: 450px;
    background: linear-gradient(180deg, #4a4a4a 0%, #2a2a2a 50%, #141414 100%);
  }
  .card--back .brand { right: 24px; top: 300px; }
  .card--back .brand__name { font-size: 21px; text-align: right; }
</style>
</head>
<body>

<section class="card card--front" aria-label="Business card front">
  <div class="brand">
    <span class="brand__mark"></span>
    <span class="brand__name">Brivo Engineering<br>Tandem</span>
  </div>

  <div class="accent-bar"></div>
  <div class="person">
    <h1 class="person__name">DANIEL HARTLEY</h1>
    <p class="person__role">Managing Director</p>
  </div>

  <address class="address">
    Brivo Engineering Tandem<br>
    24b Marlow Road, Kettering NN15 6TR
  </address>

  <ul class="contacts">
    <li>
      <svg viewBox="0 0 24 24" aria-hidden="true"><path d="M6.6 10.8a15.1 15.1 0 0 0 6.6 6.6l2.2-2.2a1 1 0 0 1 1-.25 11.4 11.4 0 0 0 3.6.57 1 1 0 0 1 1 1V20a1 1 0 0 1-1 1A17 17 0 0 1 3 4a1 1 0 0 1 1-1h3.5a1 1 0 0 1 1 1c0 1.25.2 2.45.57 3.6a1 1 0 0 1-.25 1z"/></svg>
      01536 482907
    </li>
    <li>
      <svg viewBox="0 0 24 24" aria-hidden="true"><path d="M2 5h20v2l-10 6L2 7z M2 9l10 6 10-6v10H2z"/></svg>
      sales@brivoengineering.co.uk
    </li>
    <li>
      <svg viewBox="0 0 24 24" aria-hidden="true"><circle cx="12" cy="12" r="10"/></svg>
      www.brivoengineering.co.uk
    </li>
  </ul>

  <div class="decoration" role="img" aria-label="Large brand symbol in yellow and grey belongs here"></div>
</section>

<section class="card card--back" aria-label="Business card back">
  <div class="decoration" role="img" aria-label="Large embossed brand symbol in silver and black belongs here"></div>
  <div class="brand">
    <span class="brand__mark"></span>
    <span class="brand__name">Brivo Engineering<br>Tandem</span>
  </div>
</section>

</body>
</html>
```